Business Card Design

Velora Pixel Outreach

An online marketing consulting & strategy business for the cosmetic niche

We specialise in Increasing Leads, Conversions & Content Marketing

I am looking for a very clean, BOLD business card that is simple & effective

Target Market(s)

cosmetic surgeons & cosmetic clinics

Industry/Entity Type

Marketing

Contact Information for Business Card

Dermot Kalway
Online Marketing Strategist

Dermot@VeloraPixelOutreach.example
0492 158 620

LinkedIn: in/dermotkalway

```html
<!DOCTYPE html>
<html lang="en">
<head>
<meta charset="utf-8">
<title>Velora Pixel Outreach – Business Card</title>
<link rel="stylesheet" href="https://fonts.googleapis.com/css2?family=Open+Sans:wght@400;600;700&display=swap">
<style>
  :root {
    --stage: #cfcfcf;
    --stage-light: #e6e6e6;
    --card-white: #ffffff;
    --teal-deep: #1499b5;
    --teal-light: #5ccbe8;
    --band-dark: #2f3133;
    --band-mid: #55585a;
    --brand-grey: #6a6c6e;
    --name-grey: #dadada;
    --lime: #9cc63a;
    --lime-dark: #7fae25;
    --blue: #1e94d2;
    --blue-deep: #0f7fc0;
    --text-dark: #4a4c4e;
  }
  * { box-sizing: border-box; margin: 0; padding: 0; }
  html, body {
    width: 1200px;
    height: 985px;
    overflow: hidden;
  }
  body {
    position: relative;
    background: radial-gradient(ellipse at 50% 40%, var(--stage-light), var(--stage));
    font-family: "Open Sans", Arial, sans-serif;
  }
  .card {
    position: absolute;
    overflow: hidden;
    box-shadow: 0 14px 30px rgba(0,0,0,.22);
  }

  /* Back of card */
  .card-back {
    left: 300px; top: 40px;
    width: 600px; height: 343px;
    background: linear-gradient(160deg, var(--teal-deep) 0%, var(--teal-light) 45%, var(--teal-deep) 100%);
  }
  .card-back .brand {
    position: absolute;
    left: 290px; top: 218px;
    display: flex; align-items: center; gap: 14px;
  }
  .card-back .brand-dot {
    width: 58px; height: 58px; border-radius: 50%;
    background: #ffffff;
  }
  .card-back .brand-name {
    color: #ffffff;
    font-weight: 700;
    font-size: 21px;
    line-height: 22px;
    letter-spacing: 3px;
    text-transform: uppercase;
  }

  /* Front of card */
  .card-front {
    left: 170px; top: 430px;
    width: 860px; height: 491px;
    background: var(--card-white);
  }
  .card-front .art {
    position: absolute; inset: 0;
  }
  .card-front .brand {
    position: absolute;
    left: 36px; top: 26px;
    display: flex; align-items: center; gap: 16px;
  }
  .card-front .brand-dot {
    width: 66px; height: 66px; border-radius: 50%;
    background: var(--blue);
  }
  .card-front .brand-name {
    color: var(--brand-grey);
    font-weight: 700;
    font-size: 25px;
    line-height: 27px;
    letter-spacing: 4px;
    text-transform: uppercase;
  }
  .identity {
    position: absolute;
    left: 30px; top: 145px; height: 60px;
    display: flex; align-items: center;
  }
  .identity .person {
    color: var(--name-grey);
    font-size: 26px;
    font-weight: 400;
  }
  .identity .divider {
    width: 1px; height: 32px;
    background: var(--blue);
    margin: 0 12px;
  }
  .identity .role {
    color: var(--lime);
    font-size: 20px;
    font-weight: 600;
  }
  .contacts {
    position: absolute;
    left: 400px; top: 268px;
    list-style: none;
  }
  .contacts li {
    display: flex; align-items: center; gap: 14px;
    height: 40px;
    color: var(--text-dark);
    font-size: 19px;
    font-weight: 600;
  }
  .contacts .icon {
    width: 26px; height: 26px;
    flex: none;
  }
</style>
</head>
<body>

  <section class="card card-back" aria-label="Card back">
    <div class="brand">
      <span class="brand-dot"></span>
      <span class="brand-name">Velora<br>Pixel<br>Outreach</span>
    </div>
  </section>

  <section class="card card-front" aria-label="Card front">
    <svg class="art" width="860" height="491" viewBox="0 0 860 491" aria-hidden="true">
      <defs>
        <linearGradient id="bandShade" x1="0" y1="0" x2="1" y2="0">
          <stop offset="0" stop-color="#2f3133"/>
          <stop offset="0.6" stop-color="#4a4d4f"/>
          <stop offset="1" stop-color="#2f3133"/>
        </linearGradient>
        <linearGradient id="limeShade" x1="0" y1="0" x2="0" y2="1">
          <stop offset="0" stop-color="#a8d043"/>
          <stop offset="1" stop-color="#7fae25"/>
        </linearGradient>
        <linearGradient id="blueShade" x1="0" y1="0" x2="0" y2="1">
          <stop offset="0" stop-color="#1e94d2"/>
          <stop offset="1" stop-color="#0f7fc0"/>
        </linearGradient>
      </defs>
      <!-- dark name band with rounded end -->
      <path class="name-band" d="M0 145 H770 A30 30 0 0 1 770 205 H0 Z" fill="url(#bandShade)"/>
      <!-- end disc -->
      <circle class="band-dot" cx="800" cy="212" r="42" fill="#1e94d2"/>
      <!-- bottom lime strip -->
      <polygon class="lime-strip" points="0,440 592,440 566,491 0,491" fill="url(#limeShade)"/>
      <!-- bottom blue block -->
      <polygon class="blue-block" points="612,446 860,446 860,491 586,491" fill="url(#blueShade)"/>
    </svg>

    <div class="brand">
      <span class="brand-dot"></span>
      <span class="brand-name">Velora<br>Pixel<br>Outreach</span>
    </div>

    <div class="identity">
      <span class="person">Dermot Kalway</span>
      <span class="divider"></span>
      <span class="role">Online Marketing Strategist</span>
    </div>

    <ul class="contacts">
      <li>
        <svg class="icon" viewBox="0 0 26 26" aria-hidden="true">
          <rect width="26" height="26" rx="3" fill="#1e94d2"/>
          <circle cx="13" cy="13" r="8" fill="none" stroke="#fff" stroke-width="1.6"/>
          <ellipse cx="13" cy="13" rx="3.5" ry="8" fill="none" stroke="#fff" stroke-width="1.4"/>
          <line x1="5" y1="13" x2="21" y2="13" stroke="#fff" stroke-width="1.4"/>
        </svg>
        <span>0492 158 620</span>
      </li>
      <li>
        <svg class="icon" viewBox="0 0 26 26" aria-hidden="true">
          <rect width="26" height="26" rx="3" fill="#1e94d2"/>
          <rect x="5" y="7.5" width="16" height="11" fill="none" stroke="#fff" stroke-width="1.6"/>
          <polyline points="5,7.5 13,14 21,7.5" fill="none" stroke="#fff" stroke-width="1.6"/>
        </svg>
        <span>Dermot@VeloraPixelOutreach.example</span>
      </li>
      <li>
        <svg class="icon" viewBox="0 0 26 26" aria-hidden="true">
          <rect width="26" height="26" rx="3" fill="#1e94d2"/>
        </svg>
        <span>in/dermotkalway</span>
      </li>
    </ul>
  </section>

</body>
</html>
```